Ravnaas-Lilleby Group AS

We need a design for our company including background pictures on our web (wix-template), redesign of logo and reports. Our company delivers personality test and services to clients when hiring staff or related to organizatonal developement.

Target Market(s)

Unisex, Age 30-50, managers in private corporations

Industry/Entity Type

Recruitment

Logo Text

Bygger laget sterkt (english translate: buids your team strong)

Number of Pages Required

1 page

Font styles to use
Sans Serif

Colors
add136
34a6d7
0255a3

Requirements
Must have
• The ideal designer will be the one to bring my narrative come to life. And it will have to include the testresults report and redesign (!) of my logo. Following the attached brief in ppt:
• - the testresult report
• - redesign logo
• - graphic elements in a maritime narrative
• - including the boat, the radar, 7 GULLs, the compass etc
Nice to have
• A strong narrative with a lot of elements.
• I really like the green color in the attached breif ;-)

```html
<!DOCTYPE html>
<html lang="en">
<head>
<meta charset="utf-8">
<title>Team Profile Card</title>
<link rel="stylesheet" href="https://fonts.googleapis.com/css2?family=Montserrat:wght@700&family=Oswald:wght@300;400&display=swap">
<style>
  :root {
    --parchment: #f6e5ae;
    --parchment-edge: #eab55a;
    --ink: #4d4340;
    --ink-soft: #3b3532;
    --header-gold: #f2d88b;
    --card-fill: #f8f0d2;
    --accent-red: #c8101a;
    --compass-face: #f7efcf;
    --compass-ring: #efe2b4;
    --green: #5cb832;
    --red: #d51320;
  }
  * { box-sizing: border-box; margin: 0; padding: 0; }
  html, body { width: 1200px; height: 2214px; overflow: hidden; }
  body {
    position: relative;
    background:
      radial-gradient(ellipse at 100% 0%, var(--parchment-edge) 0%, rgba(234,181,90,0) 30%),
      radial-gradient(ellipse at 100% 100%, var(--parchment-edge) 0%, rgba(234,181,90,0) 28%),
      radial-gradient(ellipse at 0% 100%, #efcd7e 0%, rgba(239,205,126,0) 25%),
      var(--parchment);
    font-family: "Oswald", sans-serif;
    color: var(--ink);
  }
  .compass {
    position: absolute; left: 163px; top: 104px;
    width: 870px; height: 870px; border-radius: 50%;
    background: radial-gradient(circle, var(--compass-face) 0%, var(--compass-face) 62%, #d9cba0 64%, var(--compass-ring) 66%, var(--compass-ring) 100%);
    box-shadow: 0 0 0 14px rgba(247,239,207,.7);
  }
  .gauge { position: absolute; }
  .gauge svg { display: block; }
  .gauge-label {
    position: absolute; font-family: "Montserrat", sans-serif; font-weight: 700;
    font-size: 49px; letter-spacing: 1px; color: var(--ink); white-space: nowrap;
  }
  .gauge--energy { left: 130px; top: 1048px; }
  .label--energy { left: 130px; top: 1196px; }
  .gauge--problem { left: 778px; top: 1040px; }
  .label--problem { left: 667px; top: 1196px; }

  .panel {
    position: absolute; top: 1346px; width: 429px; height: 440px;
    background: var(--card-fill); border: 2px solid var(--ink); border-radius: 6px; overflow: hidden;
  }
  .panel--listen { left: 55px; }
  .panel--sending { left: 708px; }
  .panel-title {
    height: 83px; background: var(--ink); color: var(--header-gold);
    font-family: "Montserrat", sans-serif; font-weight: 700; font-size: 47px;
    text-align: center; line-height: 86px; letter-spacing: 1px;
  }
  .panel-list { list-style: none; padding: 14px 0 0 58px; }
  .panel-list li {
    position: relative; font-weight: 300; font-size: 29px; line-height: 59px; color: var(--ink-soft);
  }
  .panel-list li::before {
    content: ""; position: absolute; left: -30px; top: 26px;
    width: 9px; height: 9px; border-radius: 50%; background: var(--ink-soft);
  }
  .links { position: absolute; left: 505px; top: 1362px; width: 180px; }
  .link {
    position: absolute; left: 0; width: 180px; height: 70px;
    display: flex; align-items: center; justify-content: space-between;
  }
  .link-num {
    font-family: "Montserrat", sans-serif; font-weight: 700; font-size: 58px; color: var(--accent-red);
  }
  .fields { position: absolute; left: 160px; top: 1868px; }
  .field { display: flex; align-items: baseline; font-size: 40px; height: 92px; color: var(--ink-soft); }
  .field-line { width: 870px; border-bottom: 4px dotted var(--ink-soft); margin-left: 10px; height: 34px; }
  .footer-band { position: absolute; left: 0; bottom: 0; width: 1200px; height: 32px; background: var(--ink); }
</style>
</head>
<body>
  <div class="compass" role="img" aria-label="Compass rose illustration with red and white needle pointing north"></div>

  <div class="gauge gauge--energy">
    <svg width="240" height="125" viewBox="0 0 240 125">
      <defs>
        <linearGradient id="metal" x1="0" y1="0" x2="0" y2="1">
          <stop offset="0" stop-color="#8d8d8d"/><stop offset=".4" stop-color="#f4f4f4"/><stop offset="1" stop-color="#7a7a7a"/>
        </linearGradient>
        <linearGradient id="greenFill" x1="0" y1="0" x2="0" y2="1">
          <stop offset="0" stop-color="#6fc53a"/><stop offset=".5" stop-color="#4fae2a"/><stop offset="1" stop-color="#7fcf45"/>
        </linearGradient>
        <linearGradient id="redFill" x1="0" y1="0" x2="0" y2="1">
          <stop offset="0" stop-color="#e0242c"/><stop offset=".5" stop-color="#b50d16"/><stop offset="1" stop-color="#e22e34"/>
        </linearGradient>
      </defs>
      <rect x="0" y="0" width="210" height="125" fill="url(#greenFill)"/>
      <polygon points="95,0 210,0 210,125 155,125" fill="url(#redFill)"/>
      <rect x="0" y="0" width="16" height="125" fill="url(#metal)"/>
      <rect x="196" y="0" width="16" height="125" fill="url(#metal)"/>
      <rect x="212" y="40" width="26" height="45" rx="3" fill="url(#metal)"/>
    </svg>
  </div>
  <div class="gauge-label label--energy">ENERGY</div>

  <div class="gauge gauge--problem">
    <svg width="240" height="125" viewBox="0 0 240 125">
      <rect x="0" y="0" width="210" height="125" fill="url(#greenFill)"/>
      <polygon points="135,0 210,0 210,125 185,125" fill="url(#redFill)"/>
      <rect x="0" y="0" width="16" height="125" fill="url(#metal)"/>
      <rect x="196" y="0" width="16" height="125" fill="url(#metal)"/>
      <rect x="212" y="40" width="26" height="45" rx="3" fill="url(#metal)"/>
    </svg>
  </div>
  <div class="gauge-label label--problem">PROBLEM SOLVE</div>

  <section class="panel panel--listen">
    <h2 class="panel-title">LISTEN</h2>
    <ul class="panel-list">
      <li>Lorem ipsum dolor sit amet</li><li>Lorem ipsum dolor sit amet</li><li>Lorem ipsum dolor sit amet</li><li>Lorem ipsum dolor sit amet</li><li>Lorem ipsum dolor sit amet</li>
    </ul>
  </section>

  <div class="links">
    <div class="link" style="top:0"><svg width="52" height="20"><path d="M2 10h48M2 10l12-8M2 10l12 8" stroke="#3b3532" stroke-width="5" fill="none"/></svg><span class="link-num">1</span><svg width="52" height="20"><path d="M2 10h48M50 10l-12-8M50 10l-12 8" stroke="#3b3532" stroke-width="5" fill="none"/></svg></div>
    <div class="link" style="top:92px"><svg width="52" height="20"><path d="M2 10h48M2 10l12-8M2 10l12 8" stroke="#3b3532" stroke-width="5" fill="none"/></svg><span class="link-num">2</span><svg width="52" height="20"><path d="M2 10h48M50 10l-12-8M50 10l-12 8" stroke="#3b3532" stroke-width="5" fill="none"/></svg></div>
    <div class="link" style="top:176px"><svg width="52" height="20"><path d="M2 10h48M2 10l12-8M2 10l12 8" stroke="#3b3532" stroke-width="5" fill="none"/></svg><span class="link-num">3</span><svg width="52" height="20"><path d="M2 10h48M50 10l-12-8M50 10l-12 8" stroke="#3b3532" stroke-width="5" fill="none"/></svg></div>
    <div class="link" style="top:261px"><svg width="52" height="20"><path d="M2 10h48M2 10l12-8M2 10l12 8" stroke="#3b3532" stroke-width="5" fill="none"/></svg><span class="link-num">4</span><svg width="52" height="20"><path d="M2 10h48M50 10l-12-8M50 10l-12 8" stroke="#3b3532" stroke-width="5" fill="none"/></svg></div>
    <div class="link" style="top:353px"><svg width="52" height="20"><path d="M2 10h48M2 10l12-8M2 10l12 8" stroke="#3b3532" stroke-width="5" fill="none"/></svg><span class="link-num">5</span><svg width="52" height="20"><path d="M2 10h48M50 10l-12-8M50 10l-12 8" stroke="#3b3532" stroke-width="5" fill="none"/></svg></div>
  </div>

  <section class="panel panel--sending">
    <h2 class="panel-title">SENDING</h2>
    <ul class="panel-list">
      <li>Lorem ipsum dolor sit amet</li><li>Lorem ipsum dolor sit amet</li><li>Lorem ipsum dolor sit amet</li><li>Lorem ipsum dolor sit amet</li><li>Lorem ipsum dolor sit amet</li>
    </ul>
  </section>

  <div class="fields">
    <div class="field"><span>Name :</span><span class="field-line" style="width:860px"></span></div>
    <div class="field"><span>Company :</span><span class="field-line" style="width:808px"></span></div>
    <div class="field"><span>Profile :</span><span class="field-line" style="width:838px"></span></div>
  </div>

  <div class="footer-band"></div>
</body>
</html>
```